Velmora Sports Foundation website

Velmora sports foundation is a charity organisation that assists young athletes and clubs with the financial assistance they need to progress in their sporting career.

The organisation also establishes mentoring programs to community clubs and individuals.
We envision a home page with a horizontal navigation
Contact Us
Donate: A link to a secure payment system
Meet the team: A list of names and images of the board
Lastly the link to donate should be featured prominently and several times along with cues that lead people to find out more
We prefer limited scrolling and would like to see a clean yet modern design

I am unsure if it needs to be coded or not

Target Market(s)

Potential donors, applications for funds, potential affiliates

Industry/Entity Type

Charity

Coding

Coded - Design and coding required

Number of Pages Required

5+ page

Font styles to use
Sans Serif

Colors
3176b5
ec1f27
34a7d7

Requirements
Must have
• emotionally engaging and informative
• motion enabled pictures
• links to donate
• Music
• Enable video uploads
• Large horizontal pictures of young sports players prominently soccer at this stage
• Social media presence
Nice to have
• Live chat
Should not have
• Images that depict poverty

```html
<!DOCTYPE html>
<html lang="en">
<head>
<meta charset="utf-8">
<title>Velmora Sports Foundation</title>
<link rel="stylesheet" href="https://fonts.googleapis.com/css2?family=Montserrat:wght@400;500;600&family=Open+Sans:ital,wght@0,400;0,600;1,400;1,600&family=Oswald:wght@400;500&display=swap">
<style>
:root{
  --backdrop:#1d2c3e;
  --page:#f7f7f7;
  --blue:#3176b5;
  --sky:#34a7d7;
  --red:#ec1f27;
  --navy:#1f4f96;
  --ink:#333;
  --muted:#777;
  --line:#e2e2e2;
  --card:#f0f0f0;
}
*{box-sizing:border-box;margin:0;padding:0}
html,body{width:1200px;height:2486px;overflow:hidden}
body{background:var(--backdrop);font-family:"Open Sans",Arial,sans-serif;color:var(--ink);position:relative}
.page{position:absolute;left:82px;top:25px;width:1036px;height:2461px;background:var(--page)}
.abs{position:absolute}

/* header */
.brand{left:20px;top:28px;display:flex;align-items:center;gap:12px}
.brand-dot{width:46px;height:46px;border-radius:50%;background:var(--blue)}
.brand-name{font-family:"Montserrat",sans-serif;font-weight:600;font-size:22px;color:var(--blue);line-height:1.1;width:190px}
.contact-top{left:570px;top:28px;display:flex;gap:14px;align-items:center;font-size:14px;color:#666;line-height:1.55}
.btn-donate{display:inline-flex;align-items:center;gap:8px;background:var(--red);color:#fff;font-family:"Oswald",sans-serif;font-size:17px;border-radius:24px;padding:0 16px 0 8px;height:44px;text-decoration:none;box-shadow:0 2px 0 #b3141a}
.btn-donate .coin{width:26px;height:26px;border-radius:50%;border:2px solid #fff;display:flex;align-items:center;justify-content:center;font-size:15px;font-family:"Montserrat",sans-serif}
.header-donate{left:886px;top:25px}

/* nav */
.nav{left:316px;top:104px;width:702px;height:67px;display:flex}
.nav a{display:flex;flex-direction:column;align-items:center;justify-content:center;gap:8px;background:var(--sky);color:#fff;font-family:"Montserrat",sans-serif;font-size:13px;font-weight:500;text-decoration:none;border-left:1px solid rgba(255,255,255,.25)}
.nav a.home{background:#ef5b5b;clip-path:polygon(14px 0,100% 0,100% 100%,0 100%);border:0}
.nav svg{width:22px;height:22px}

/* hero */
.hero{left:17px;top:171px;width:1001px;height:464px;background:linear-gradient(180deg,#8e8a84 0%,#a9a39a 35%,#6f7860 62%,#3f8a2e 78%,#2f7a22 100%)}
.hero-panel{left:605px;top:107px;width:323px;height:249px;background:rgba(236,31,39,.9);outline:3px solid rgba(255,255,255,.6);outline-offset:-6px;padding:22px 26px}
.hero-title{font-family:"Oswald",sans-serif;font-size:48px;font-weight:500;color:#fff;line-height:1.12}
.hero-btn{display:inline-block;margin-top:26px;border:2px solid #fff;color:#fff;font-family:"Montserrat",sans-serif;font-size:14px;padding:10px 20px}
.dots{display:flex;gap:10px;margin-top:24px}
.dots span{width:11px;height:11px;border-radius:50%;background:#fff}
.dots span:first-child{box-shadow:0 0 0 3px rgba(255,255,255,.5)}

/* feature cards */
.cards{left:17px;top:649px;width:1001px;display:flex;gap:17px}
.card{flex:1;height:284px;background:var(--card);border:1px solid #ddd;text-align:center;padding:22px 30px}
.card-icon{width:100px;height:100px;border-radius:50%;background:var(--sky);border:4px solid #fff;box-shadow:0 0 0 1px #d8d8d8;margin:0 auto 20px;display:flex;align-items:center;justify-content:center}
.card-icon svg{width:44px;height:44px}
.card h3{font-family:"Montserrat",sans-serif;font-weight:400;font-size:19px;color:#555;margin-bottom:8px}
.card p{font-size:11.5px;line-height:1.75;color:var(--muted)}
.read{display:inline-block;margin-top:14px;font-size:11.5px;color:#333;font-family:"Montserrat",sans-serif}

/* welcome */
.welcome{left:17px;top:990px;width:1001px;text-align:center}
.welcome h2{font-family:"Montserrat",sans-serif;font-weight:500;font-size:29px;color:#333;letter-spacing:.3px}
.welcome p{margin:16px auto 0;width:900px;font-size:11.5px;line-height:1.75;color:var(--muted)}
.welcome .btn-donate{margin-top:22px}
.rule{left:17px;width:1001px;height:1px;background:var(--line)}

/* video + team */
.sec-title{font-family:"Montserrat",sans-serif;font-weight:500;font-size:25px;color:#333}
.video{left:17px;top:1324px;width:476px;height:298px;background:linear-gradient(180deg,#8fa0a8 0%,#7f9b77 55%,#3f6d34 100%)}
.video-bar{position:absolute;left:0;top:0;right:0;height:40px;background:rgba(40,40,40,.75);color:#fff;font-size:12px;padding:0 14px;display:flex;align-items:center;justify-content:space-between}
.play{position:absolute;left:212px;top:156px;width:52px;height:36px;border:2px solid #fff;border-radius:8px;background:rgba(0,0,0,.3);display:flex;align-items:center;justify-content:center}
.team-arrows{left:986px;top:1285px;font-size:22px;color:#555;font-family:"Montserrat",sans-serif;letter-spacing:-2px}
.member{left:544px;width:474px;display:flex;gap:28px}
.avatar{width:100px;height:100px;border-radius:50%;flex:none;background:radial-gradient(circle at 50% 40%,#c9a98c,#6f5a48);border:3px solid #fff;box-shadow:0 0 0 1px #ccc}
.quote{font-style:italic;font-size:11.5px;line-height:1.75;color:#666;padding-top:8px}
.quote b{font-size:20px;color:#999;font-weight:400}
.who{margin-top:12px;font-size:12.5px;color:var(--navy)}
.stars{margin-top:6px;font-size:11px;color:#f1b434;letter-spacing:1px}
.stars i{color:#bbb;font-style:normal}

/* news */
.news{left:17px;top:1695px;width:1001px;height:393px;background:linear-gradient(180deg,#1f5fa9,#2868b2 60%,#2f6fb6)}
.news h2{position:absolute;left:0;right:0;top:60px;text-align:center;font-family:"Oswald",sans-serif;font-weight:500;font-size:30px;color:#fff}
.post{top:126px;width:444px;height:187px;background:#fff;padding:12px;display:flex;gap:18px}
.post-img{width:156px;height:163px;flex:none}
.post h4{font-family:"Oswald",sans-serif;font-weight:400;font-size:16px;color:#333;margin-top:6px}
.post .date{font-style:italic;font-weight:600;font-size:13px;color:var(--navy);margin-top:12px}
.post p{font-size:11.5px;line-height:1.75;color:#666;margin-top:8px}
.post .read{margin-top:8px;color:var(--navy)}

/* footer */
.foot h5{font-family:"Montserrat",sans-serif;font-weight:500;font-size:16px;color:#333;margin-bottom:14px}
.foot p,.foot li{font-size:12px;line-height:1.7;color:#555}
.nl-input{width:245px;height:42px;border:1px solid #ccc;background:#fff;font-size:11px;padding:0 14px;display:flex;align-items:center;margin-top:14px;color:#555}
.nl-btn{display:inline-block;margin-top:12px;border:1px solid var(--navy);color:var(--navy);font-family:"Montserrat",sans-serif;font-size:13px;padding:8px 16px}
.c-row{display:flex;gap:14px;margin-bottom:14px;font-size:13px;color:#555;line-height:1.6}
.c-row svg{flex:none;width:14px;height:14px;margin-top:3px}
.links{list-style:none}
.links li{font-size:12px;line-height:22.5px}
.f-brand{left:826px;top:2150px;width:170px;text-align:center}
.f-brand .brand-dot{margin:0 auto 8px}
.f-brand .brand-name{width:auto;font-size:19px}
.chat{display:inline-block;margin-top:22px;background:var(--navy);color:#fff;font-family:"Montserrat",sans-serif;font-weight:600;font-size:13px;padding:8px 22px;border-radius:3px}
.socials{left:0;width:1036px;top:2388px;display:flex;justify-content:center;gap:6px}
.socials span{width:26px;height:26px;border-radius:50%;border:1px solid #9ab;background:#fff}
.socials span.tube{border-color:var(--red)}
.copy{left:0;width:1036px;top:2430px;text-align:center;font-size:11.5px;color:#555}
</style>
</head>
<body>
<div class="page">

  <header>
    <div class="abs brand"><span class="brand-dot"></span><span class="brand-name">Velmora Sports Foundation</span></div>
    <div class="abs contact-top">
      <svg width="22" height="30" viewBox="0 0 22 30"><path d="M5 2 L9 2 L10 9 L7 11 Q9 18 14 22 L17 19 L21 22 L20 27 Q12 29 6 20 Q1 11 5 2Z" fill="#8a8a8a"/></svg>
      <div>info@velmorasportsfoundation.org<br>Phone : (555) - 014 - 2270</div>
    </div>
    <a class="abs btn-donate header-donate" href="#"><span class="coin">$</span>DONATE NOW</a>
    <nav class="abs nav">
      <a class="home" style="width:119px" href="#"><svg viewBox="0 0 24 24" fill="none" stroke="#fff" stroke-width="2"><path d="M3 11 12 3l9 8M5 10v10h5v-6h4v6h5V10"/></svg>HOME</a>
      <a style="width:124px" href="#"><svg viewBox="0 0 24 24" fill="none" stroke="#fff" stroke-width="2"><rect x="3" y="5" width="18" height="16"/><path d="M3 10h18M8 3v4M16 3v4"/></svg>PROGRAM</a>
      <a style="width:124px" href="#"><svg viewBox="0 0 24 24" fill="none" stroke="#fff" stroke-width="2"><path d="M3 3h9l9 9-9 9-9-9z"/><circle cx="8" cy="8" r="1.5"/></svg>DONATE</a>
      <a style="width:169px" href="#"><svg viewBox="0 0 24 24" fill="none" stroke="#fff" stroke-width="2"><path d="M8 3 3 6l2 5 2-1v11h10V10l2 1 2-5-5-3q-4 4-8 0z"/></svg>MEET THE TEAM</a>
      <a style="width:166px" href="#"><svg viewBox="0 0 24 24" fill="none" stroke="#fff" stroke-width="2"><rect x="3" y="5" width="18" height="14"/><path d="m3 6 9 7 9-7"/></svg>CONTACT US</a>
    </nav>
  </header>

  <section class="abs hero" role="img" aria-label="Young soccer player in a red jersey celebrating with a ball in a packed stadium">
    <div class="abs hero-panel">
      <div class="hero-title">Velmora Sports Foundation</div>
      <span class="hero-btn">MORE INFORMATION</span>
      <div class="dots"><span></span><span></span><span></span><span></span></div>
    </div>
  </section>

  <section class="abs cards">
    <article class="card">
      <div class="card-icon"><svg viewBox="0 0 44 44" fill="#fff"><circle cx="22" cy="13" r="6"/><circle cx="10" cy="17" r="4.5"/><circle cx="34" cy="17" r="4.5"/><path d="M12 34q0-13 10-13t10 13zM2 32q0-9 8-9 3 0 4 1-4 4-4 8zM42 32q0-9-8-9-3 0-4 1 4 4 4 8z"/></svg></div>
      <h3>Community Clubs</h3>
      <p>Sed ut perspiciatis unde omnis iste natus error sit voluptatem accusantium doloremque laudantium, totam rem aperiam, eaque ipsa quae</p>
      <span class="read">READ MORE ➜</span>
    </article>
    <article class="card">
      <div class="card-icon"><svg viewBox="0 0 44 44" fill="#fff"><circle cx="22" cy="14" r="8"/><path d="M8 38q0-14 14-14t14 14z"/></svg></div>
      <h3>Individuals</h3>
      <p>Sed ut perspiciatis unde omnis iste natus error sit voluptatem accusantium doloremque laudantium, totam rem aperiam, eaque ipsa quae</p>
      <span class="read">READ MORE ➜</span>
    </article>
    <article class="card">
      <div class="card-icon"><svg viewBox="0 0 44 44"><path d="M14 4h16l-3 6H17z" fill="#fff"/><rect x="10" y="12" width="24" height="28" rx="2" fill="#fff"/><text x="22" y="32" text-anchor="middle" font-family="Montserrat,sans-serif" font-size="14" fill="#34a7d7">$</text></svg></div>
      <h3>Donate</h3>
      <p>Sed ut perspiciatis unde omnis iste natus error sit voluptatem accusantium doloremque laudantium, totam rem aperiam, eaque ipsa quae</p>
      <span class="read">READ MORE ➜</span>
    </article>
  </section>

  <section class="abs welcome">
    <h2>WELCOME TO VELMORA SPORTS FOUNDATION</h2>
    <p>Sed ut perspiciatis unde omnis iste natus error sit voluptatem accusantium doloremque laudantium, totam rem aperiam, eaque ipsa quae ab illo inventore veritatis et quasi architecto beatae vitae dicta sunt explicabo. Nemo enim ipsam voluptatem quia voluptas sit aspernatur aut odit aut fugit, sed quia consequuntur magni dolores eos qui ratione voluptatem sequi nesciunt. Neque porro quisquam est, qui dolorem ipsum quia dolor sit amet, consectetur, adipisci velit, sed quia non numquam</p>
    <a class="btn-donate" href="#"><span class="coin">$</span>DONATE NOW</a>
  </section>

  <div class="abs rule" style="top:1215px"></div>

  <h2 class="abs sec-title" style="left:17px;top:1278px">VELMORA SPORTS FOUNDATION</h2>
  <div class="abs video" role="img" aria-label="Video still of two youth soccer players contesting the ball on a pitch">
    <div class="video-bar"><span>Velmora sports foundation</span><span>⋖</span></div>
    <div class="play"><svg width="16" height="18" viewBox="0 0 16 18"><path d="M2 1l13 8-13 8z" fill="#fff"/></svg></div>
  </div>

  <h2 class="abs sec-title" style="left:544px;top:1278px">MEET THE TEAM</h2>
  <div class="abs team-arrows">‹›</div>
  <div class="abs member" style="top:1347px">
    <div class="avatar" role="img" aria-label="Portrait of a board member"></div>
    <div>
      <p class="quote"><b>“</b> Nemo enim ipsam voluptatem quia voluptas sit aspernatur aut odit aut fugit, sed quia consequuntur magni dolores eos qui ratione voluptatem sequi nesciunt.</p>
      <p class="who">John doe - Sports Foundation</p>
      <p class="stars">★★★<i>☆☆</i></p>
    </div>
  </div>
  <div class="abs rule" style="left:544px;width:474px;top:1484px"></div>
  <div class="abs member" style="top:1513px">
    <div class="avatar" role="img" aria-label="Portrait of a board member" style="background:radial-gradient(circle at 50% 40%,#d9b79a,#8a6b4e)"></div>
    <div>
      <p class="quote"><b>“</b> Nemo enim ipsam voluptatem quia voluptas sit aspernatur aut odit aut fugit, sed quia consequuntur magni dolores eos qui ratione voluptatem sequi nesciunt.</p>
      <p class="who">John doe - Sports Foundation</p>
      <p class="stars">★★★<i>☆☆</i></p>
    </div>
  </div>

  <section class="abs news">
    <h2>NEWS &amp; BLOG</h2>
    <article class="abs post" style="left:45px">
      <div class="post-img" role="img" aria-label="Youth soccer team posing together with a ball" style="background:linear-gradient(180deg,#7d8a94,#3f4d3c 70%,#5e8a44)"></div>
      <div>
        <h4>Nulla at diam ornare, aliquam urna</h4>
        <p class="date">MAY 25, 2016</p>
        <p>Nulla at diam ornare, aliquam urna vel, modo urna. Nam id risus a est luctus consectetur quis eget libero. Suspendisse potenti.</p>
        <span class="read">READ MORE ➜</span>
      </div>
    </article>
    <article class="abs post" style="left:514px">
      <div class="post-img" role="img" aria-label="Close-up of a player's boots striking a soccer ball" style="background:linear-gradient(180deg,#2b3f6a,#3d6b3a 60%,#5e9a3c)"></div>
      <div>
        <h4>Nulla at diam ornare, aliquam urna</h4>
        <p class="date">MAY 25, 2016</p>
        <p>Nulla at diam ornare, aliquam urna vel, modo urna. Nam id risus a est luctus consectetur quis eget libero. Suspendisse potenti.</p>
        <span class="read">READ MORE ➜</span>
      </div>
    </article>
  </section>

  <footer class="foot">
    <div class="abs" style="left:37px;top:2151px;width:260px">
      <h5>SIGN UP FOR NEWSLETTER</h5>
      <p>Excepteur sint occaecat cupidatat non proident, sunt in culpa qui officia deserunt</p>
      <div class="nl-input">Enter email</div>
      <span class="nl-btn">SUBSCRIPTION</span>
    </div>
    <div class="abs" style="left:365px;top:2151px;width:270px">
      <h5>CONTACT US</h5>
      <div class="c-row"><svg viewBox="0 0 14 14"><path d="M7 1a4.5 4.5 0 0 0-4.5 4.5C2.5 9 7 13 7 13s4.5-4 4.5-7.5A4.5 4.5 0 0 0 7 1z" fill="#555"/><circle cx="7" cy="5.5" r="1.6" fill="#f7f7f7"/></svg><span>Velmora sports foundation<br>48 Linden Ridge Rd. Ashford, Nc,<br>27500</span></div>
      <div class="c-row"><svg viewBox="0 0 14 14"><path d="M3 1h3l1 3-2 1q1 3 4 4l1-2 3 1v3q-6 1-9-3T3 1z" fill="#555"/></svg><span>Phone:&nbsp; 555-019-4476</span></div>
      <div class="c-row"><svg viewBox="0 0 14 14"><rect x="1" y="3" width="12" height="8" fill="#555"/><path d="m1 3 6 5 6-5" stroke="#f7f7f7" fill="none"/></svg><span>Email: info@velmorasports.org</span></div>
    </div>
    <div class="abs" style="left:675px;top:2151px">
      <h5>QUICK LINKS</h5>
      <ul class="links"><li>Home</li><li>About Us</li><li>Program</li><li>Donate</li><li>Meet the Team</li><li>Contact Us</li></ul>
    </div>
    <div class="abs f-brand">
      <div class="brand-dot" style="width:60px;height:60px"></div>
      <div class="brand-name">Velmora Sports Foundation</div>
      <span class="chat">LIVE CHAT</span>
    </div>
    <div class="abs rule" style="top:2361px"></div>
    <div class="abs socials"><span></span><span></span><span></span><span class="tube"></span></div>
    <p class="abs copy">©2015 - 2016 Velmora sports foundation. All Rights Reserved.</p>
  </footer>
</div>
</body>
</html>
```